We need 3 A2 posters similar look but different enough to be eye catching when changed.

We are a healthcare centre that requires 3 A2 posters - simple, similar but different background colours. These posters will be used within our business to promote services we provide to our clients.

The design should include our logo(attached), a large header and a large section in the middle of the poster to promote the event. We need a blank text box (which WE can insert text to advertise), and 1 image to advertise the event. Please note, we do not need you to choose an image we simply would like you to place a demo to give us an idea of where it should sit.

We want to use the bubble design (attached) as a background and the company colours pink, orange and blue - as on our website. Attached is a copy of our logo and background bubble effect. You can also refer to our website - www.tallowbrookwellness.com.au for more inspiration.

Just to reiterate, these posters should be simple, different but have a uniform feel. They should have an empty middle section that can be edited to add text and a space for an eye catching title and matching image.

Our services include Chiropractic, Podiatry, Nutrition, Massage, Yoga, Pilates and Specialised rehabilitation classes.

Reason: Hi designers, I know we are all busy but I really need more designs from the designers I invited to this project and look forward to receiving more designs. Any questions please let me know. Regards, Marion

Reason: Hi all Increased the budget Regards Marion

Corporate Sydney City office workers

Healthcare

• logo and company colours
section in the middles that can be edited to add text
Space allocated for image placement
Catchy title/header

```html
<!DOCTYPE html>
<html lang="en">
<head>
<meta charset="utf-8">
<title>Tallowbrook Wellness – Poster</title>
<link rel="stylesheet" href="https://fonts.googleapis.com/css2?family=Mulish:wght@700;800&display=swap">
<style>
  :root {
    --orange: #d78c45;
    --purple: #bf2fe0;
    --blue: #6182f9;
    --peach: #e8c7a6;
    --peach-deep: #e6bca6;
    --white: #ffffff;
    --page: #ffffff;
  }
  html, body {
    margin: 0;
    padding: 0;
    width: 934px;
    height: 1200px;
    overflow: hidden;
    background: var(--page);
    font-family: "Mulish", "Century Gothic", sans-serif;
  }
  .poster {
    position: absolute;
    left: 86px;
    top: 53px;
    width: 757px;
    height: 1071px;
    overflow: hidden;
    box-shadow: 0 10px 40px rgba(0,0,0,0.22);
  }
  .poster__backdrop {
    position: absolute;
    inset: 0;
    background: linear-gradient(160deg, var(--peach) 0%, var(--peach-deep) 50%, var(--peach) 100%);
  }
  .top-strip { position: absolute; top: 0; height: 17px; }
  .top-strip--blue { left: 0; width: 527px; background: var(--blue); }
  .top-strip--orange { left: 527px; width: 69px; background: var(--orange); }
  .top-strip--purple { left: 596px; width: 161px; background: var(--purple); }
  .header-banner {
    position: absolute;
    left: 26px;
    top: 17px;
    width: 701px;
    height: 111px;
    background: var(--orange);
    border-radius: 0 0 14px 14px;
    box-shadow: 0 3px 6px rgba(0,0,0,0.15);
  }
  .header-banner__title {
    position: absolute;
    right: 26px;
    top: 38px;
    margin: 0;
    font-size: 45px;
    font-weight: 800;
    color: var(--white);
    line-height: 1;
  }
  .content-box {
    position: absolute;
    left: 86px;
    top: 364px;
    width: 587px;
    height: 567px;
    background: var(--white);
    border: 4px solid var(--orange);
    border-radius: 14px;
    box-shadow: 0 3px 6px rgba(0,0,0,0.15);
  }
  .content-box__text {
    position: absolute;
    left: 11px;
    top: 142px;
    width: 575px;
    margin: 0;
    font-size: 19.5px;
    font-weight: 800;
    line-height: 27px;
    color: var(--orange);
  }
  .content-box__text p { margin: 0 0 27px; }
  .image-slot {
    position: absolute;
    left: 377px;
    top: 154px;
    width: 344px;
    height: 314px;
    border: 3px solid var(--orange);
    border-radius: 14px;
    background: linear-gradient(180deg, #f7f5f2 0%, #ece6dc 45%, #f3f1ee 70%, #e8e3dc 100%);
    box-shadow: 0 3px 6px rgba(0,0,0,0.15);
  }
  .web-address {
    position: absolute;
    right: 19px;
    top: 962px;
    margin: 0;
    font-size: 19px;
    font-weight: 800;
    color: var(--white);
  }
  .footer-band {
    position: absolute;
    left: 0;
    top: 990px;
    width: 757px;
    height: 81px;
    background: var(--purple);
  }
  .brand-name {
    position: absolute;
    right: 24px;
    top: 30px;
    margin: 0;
    font-size: 28px;
    font-weight: 800;
    color: var(--white);
    line-height: 1;
  }
</style>
</head>
<body>
  <main class="poster">
    <div class="poster__backdrop" role="img" aria-label="Soft peach background with faint pink rounded bubble shapes"></div>

    <div class="top-strip top-strip--blue"></div>
    <div class="top-strip top-strip--orange"></div>
    <div class="top-strip top-strip--purple"></div>

    <header class="header-banner">
      <h1 class="header-banner__title">Header text space</h1>
    </header>

    <section class="content-box">
      <div class="content-box__text">
        <p>Welcome to Tallowbrook Wellness. Our goal is to achieve the best possible health outcome for our patients. Our unique combination of therapies, structural correction and individualised exercise programs is what sets us apart.</p>
        <p>At anytime, if you have a health condition, even if you feel it is not something we could help you with, contact us and we will find the right solution for you. We are here for the health of our community"</p>
      </div>
    </section>

    <div class="image-slot" role="img" aria-label="Photo placeholder: a client relaxing on a massage table in a bright treatment room"></div>

    <p class="web-address">www.tallowbrookwellness.com.au</p>

    <footer class="footer-band">
      <p class="brand-name">Tallowbrook Wellness</p>
    </footer>
  </main>
</body>
</html>
```